WordPress Design for both website and landing page for an expert

I need a clean and stylish design for my new website. I work as an expert (see attached file WHY HOW WHAT), my product is expert opinion (reports) for company evaluations You can use all of the attached pictures colored or black / white. The person is me, you can add other pictures, if you want. The design should be clean and stylish, so you could use white, black, gray, silver and / or one additional color. I have added an idea about my website, see attached file CONCEPT WEBSITE If you have any more information, please do not hesitate to contact us 'Hesitate to ask me ...

```html
<!DOCTYPE html>
<html lang="de">
<head>
<meta charset="utf-8">
<title>Lukas Brenner – Sachverständiger für Firmenbewertungen</title>
<link rel="stylesheet" href="https://fonts.googleapis.com/css2?family=Montserrat:wght@400;500;600&family=Open+Sans:wght@400;600&display=swap">
<style>
:root{
  --red:#d0102b;
  --black:#000;
  --dark:#353535;
  --card:#efefef;
  --text:#222;
  --muted:#555;
  --line:#cfcfcf;
  --white:#fff;
}
*{margin:0;padding:0;box-sizing:border-box}
html,body{width:1200px;height:2209px;overflow:hidden;background:var(--white)}
body{position:relative;font-family:"Open Sans",Arial,sans-serif;color:var(--text)}
.abs{position:absolute}
/* header */
.site-header{left:0;top:0;width:1200px;height:96px;background:var(--black)}
.brand{left:144px;top:28px;display:flex;align-items:center;gap:10px;color:var(--white);font-family:"Montserrat",sans-serif;font-weight:400;font-size:17px;letter-spacing:3px;text-transform:uppercase}
.brand-dot{width:14px;height:14px;border-radius:50%;background:var(--white)}
.main-nav{top:38px;left:0;width:1200px;height:20px}
.main-nav a{position:absolute;color:#cfcfcf;text-decoration:none;font-family:"Montserrat",sans-serif;font-size:12.6px;text-transform:uppercase;white-space:nowrap}
.main-nav a.active{color:var(--white);text-decoration:underline;text-underline-offset:5px}
/* hero */
.hero-photo{left:0;top:96px;width:1200px;height:596px;background:linear-gradient(90deg,#d9d8d5 0%,#cfcdc9 45%,#b9a99b 62%,#e6e2dc 80%,#c9c4bd 100%)}
.hero-cut{left:0;top:600px}
.hero-title{left:144px;top:232px;font-family:"Montserrat",sans-serif;font-weight:500;font-size:31px;line-height:41px;color:var(--red);text-transform:uppercase;white-space:nowrap}
.hero-sub{left:144px;top:314px;font-size:18px;line-height:26px;color:#111;white-space:nowrap}
.btn{display:flex;align-items:center;justify-content:center;background:var(--red);color:var(--white);font-family:"Montserrat",sans-serif;font-weight:600;font-size:16px;text-transform:uppercase;border-radius:2px;text-decoration:none}
.hero-btn{left:144px;top:377px;width:136px;height:50px}
.slider-arrow{top:342px}
/* reasons */
.reasons-title{left:144px;top:756px;font-family:"Montserrat",sans-serif;font-weight:500;font-size:30px;line-height:40px;color:var(--red);white-space:nowrap}
.reason-card{background:var(--card);border-radius:2px;padding:19px 0 0 19px}
.reason-card h3{font-family:"Montserrat",sans-serif;font-weight:600;font-size:19.5px;line-height:24px;color:#111;margin:10px 0 6px}
.reason-card p{font-size:10.6px;line-height:19px;color:var(--muted);white-space:nowrap}
.card-fast{left:144px;top:860px;width:217px;height:225px}
.card-cert{left:373px;top:969px;width:217px;height:240px}
.card-clear{left:144px;top:1100px;width:217px;height:202px}
/* faq */
.faq-title{left:645px;top:758px;font-family:"Montserrat",sans-serif;font-weight:500;font-size:29px;color:#111}
.faq-list{left:645px;top:860px;width:411px;list-style:none;border-top:1px solid var(--line)}
.faq-list li{border-bottom:1px solid var(--line);display:flex;gap:9px;font-size:14px;line-height:21px;color:#333;padding:0 0 0 2px;white-space:nowrap}
.faq-list li svg{flex:none;margin-top:5px}
/* dark band */
.dark-band{left:0;top:1380px}
.band-photo{left:610px;top:1383px;width:446px;height:387px;border-radius:2px;background:linear-gradient(135deg,#8a7563 0%,#d9cfc3 35%,#eef0f2 60%,#a6b1bd 100%)}
.band-lead{left:144px;top:1542px;font-size:17px;line-height:28px;color:var(--white);white-space:nowrap}
.band-note{left:146px;top:1640px;font-size:12px;line-height:20px;color:#c9c9c9;white-space:nowrap}
.band-btn{left:145px;top:1723px;width:136px;height:48px}
/* promise */
.promise{left:0;top:1914px;width:1200px;text-align:center;font-size:17px;line-height:29px;color:var(--red)}
.promise-btn{left:532px;top:1983px;width:136px;height:50px}
/* footer */
.site-footer{left:0;top:2113px;width:1200px;height:96px;background:var(--black)}
.footer-nav{left:144px;top:2138px;font-size:11px;color:#cfcfcf;white-space:nowrap;word-spacing:2px}
.footer-nav span{margin:0 8px}
.copyright{left:144px;top:2165px;font-size:11px;color:#bdbdbd;word-spacing:2px}
.social{left:1003px;top:2153px;display:flex;gap:22px}
.social span{width:14px;height:14px;border-radius:50%;background:#cfcfcf}
</style>
</head>
<body>

<header class="site-header abs"></header>
<div class="brand abs"><span class="brand-dot"></span>Lukas Brenner</div>
<nav class="main-nav abs">
  <a class="active" href="#" style="left:502px">Home</a>
  <a href="#" style="left:577px">What I do</a>
  <a href="#" style="left:682px">Why I do it &amp; how I do it</a>
  <a href="#" style="left:889px">About me</a>
  <a href="#" style="left:993px">Contact</a>
</nav>

<div class="hero-photo abs" role="img" aria-label="Portrait photo of the expert leaning on a railing in a bright concrete building"></div>
<svg class="hero-cut abs" width="1200" height="93" viewBox="0 0 1200 93"><polygon points="0,92 1200,11 1200,93 0,93" fill="#fff"/></svg>
<h1 class="hero-title abs">Sachverständiger für<br>Firmenbewertungen -</h1>
<p class="hero-sub abs">Sie benötigen ein Gutachten zur Ermittlung des<br>Wertes Ihres Unternehmens</p>
<a class="btn hero-btn abs" href="#">Contact us</a>
<svg class="slider-arrow abs" style="left:55px" width="14" height="24" viewBox="0 0 14 24"><polyline points="12,2 3,12 12,22" fill="none" stroke="#444" stroke-width="3.5"/></svg>
<svg class="slider-arrow abs" style="left:1128px" width="14" height="24" viewBox="0 0 14 24"><polyline points="2,2 11,12 2,22" fill="none" stroke="#444" stroke-width="3.5"/></svg>

<h2 class="reasons-title abs">3 reasons, why you should<br>work with me</h2>

<article class="reason-card card-fast abs">
  <svg width="66" height="66" viewBox="0 0 66 66" fill="none" stroke="#d0102b" stroke-width="2"><circle cx="33" cy="33" r="30"/><circle cx="33" cy="33" r="24" stroke-width="1.5"/><line x1="33" y1="33" x2="33" y2="17"/><line x1="33" y1="33" x2="44" y2="33"/><circle cx="33" cy="33" r="2" fill="#d0102b"/></svg>
  <h3>Schnell</h3>
  <p>Sie bekommen Ihr Gutachten<br>zeitnah (innerhalb von max. 21<br>Tagen nach Zugang aller benötig-<br>ten Unterlagen)</p>
</article>

<article class="reason-card card-cert abs">
  <svg width="62" height="64" viewBox="0 0 62 64" fill="none" stroke="#d0102b" stroke-width="2"><rect x="4" y="3" width="48" height="54" rx="3"/><line x1="13" y1="15" x2="43" y2="15"/><line x1="13" y1="23" x2="43" y2="23"/><line x1="13" y1="31" x2="36" y2="31"/><line x1="13" y1="39" x2="30" y2="39"/><circle cx="47" cy="48" r="8"/><polyline points="42,55 40,63 47,59 54,63 52,55"/></svg>
  <h3>Zertifiziert</h3>
  <p>Sie erhalten ein qualifiziertes und<br>belastbares Gutachten von einem<br>zertifizierten Sachverständigen<br>(höchste Akzeptanz bei allen<br>Parteien)</p>
</article>

<article class="reason-card card-clear abs">
  <svg width="64" height="64" viewBox="0 0 64 64" fill="none" stroke="#d0102b" stroke-width="2"><rect x="2" y="2" width="60" height="60"/><circle cx="32" cy="28" r="14"/><circle cx="32" cy="28" r="5"/><line x1="32" y1="8" x2="32" y2="14"/><line x1="32" y1="42" x2="32" y2="48"/><line x1="12" y1="28" x2="18" y2="28"/><line x1="46" y1="28" x2="52" y2="28"/><circle cx="14" cy="50" r="5"/><circle cx="50" cy="50" r="5"/></svg>
  <h3>Verständlich</h3>
  <p>Ihr Gutachten wird für Sie logisch<br>und nachvollziehbar sein und kein<br>"Fachchinesisch" enthalten</p>
</article>

<h2 class="faq-title abs">FAQ</h2>
<ul class="faq-list abs">
  <li style="height:60px;align-items:center"><svg width="12" height="12" viewBox="0 0 12 12"><rect width="12" height="12" rx="2" fill="#777"/><path d="M6 3v6M3 6h6" stroke="#fff" stroke-width="1.6"/></svg>Was sind die Kaufmotive der Kunden?</li>
  <li style="height:87px;padding-top:20px"><svg width="12" height="12" viewBox="0 0 12 12"><rect width="12" height="12" rx="2" fill="#777"/><path d="M6 3v6M3 6h6" stroke="#fff" stroke-width="1.6"/></svg><span>Sie wollen Anteile Ihres Unternehmens oder ihr<br>gesamtes Unternehmen verkaufen?</span></li>
  <li style="height:105px;padding-top:20px"><svg width="12" height="12" viewBox="0 0 12 12"><rect width="12" height="12" rx="2" fill="#777"/><path d="M6 3v6M3 6h6" stroke="#fff" stroke-width="1.6"/></svg><span>Sie wollen Ihr Unternehmen auf Ihre Erben übertra-<br>gen und benötigen eine Bewertung für das Finan-<br>zamt?</span></li>
  <li style="height:106px;padding-top:20px"><svg width="12" height="12" viewBox="0 0 12 12"><rect width="12" height="12" rx="2" fill="#777"/><path d="M6 3v6M3 6h6" stroke="#fff" stroke-width="1.6"/></svg><span>Sie müssen im Rahmen einer Trennung/Scheidung<br>jemanden ausbezahlen und benötigen eine Bemes-<br>sungsgrundlage?</span></li>
</ul>

<svg class="dark-band abs" width="1200" height="464" viewBox="0 0 1200 464"><polygon points="0,100 1200,19 1200,464 0,464" fill="#353535"/></svg>
<div class="band-photo abs" role="img" aria-label="Photo of a hand with a pen reviewing financial charts on a desk"></div>
<p class="band-lead abs">Lassen Sie Ihr Unternehmen von einem qualifizer-<br>ten Sachverständigen bewerten und gehen somit<br>vielen (unnötigen) Streitereien aus dem Weg.</p>
<p class="band-note abs">Merke: Die Kosten für ein Gutachten sind immer überproportional güns-<br>tiger als die Kosten für Rechtsstreitigkeiten. Und das losgelöst von der<br>psychischen Belastung einer solchen Auseinandersetzung ...</p>
<a class="btn band-btn abs" href="#">Reda more</a>

<p class="promise abs">Mein Qualitätsversprechen: Sollte der avisierte Termin für die Erstellung des Gutachtens überschritten werden,<br>erhalten Sie das Gutachten absolut kostenfrei! (Ich verzichte auf mein Honorar)</p>
<a class="btn promise-btn abs" href="#">Reda more</a>

<footer class="site-footer abs"></footer>
<nav class="footer-nav abs">Home<span>|</span>What I Do<span>|</span>Why I Do It &amp; How I Do It<span>|</span>About Me<span>|</span>Contact</nav>
<p class="copyright abs">Copyright © 2018 Lukas Brenner. All rights reserved.</p>
<div class="social abs"><span></span><span></span></div>

</body>
</html>
```